Legal firm website redesign

Existing site for Sydney CBD lawyer needs clean and professional redesign - http://brintonlaw.com.au

The site will be viewed by a wide range of users: businesses, individuals, referral partners and other lawyers.

Please see the list of must haves for further details

Target Market(s)

Businesses, individuals, referral partners and other lawyers

Industry/Entity Type

Lawyer

Requirements
Must have
• Prominent display of phone number.
List of services down the left hand side of the site (5x services or so).
Search box in header.
Please use the greys and blues from the existing header.
New header must include the wording "Efficiency - Fulfillment - Integrity - Teamwork"

```html
<!DOCTYPE html>
<html lang="en">
<head>
<meta charset="utf-8">
<title>Brinton Law – Commercial Lawyers Sydney</title>
<link href="https://fonts.googleapis.com/css2?family=Open+Sans:wght@400;600;700&family=Arimo:wght@400&display=swap" rel="stylesheet">
<style>
  :root{
    --header-dark:#333333;
    --header-mid:#565656;
    --panel-grey:#f2f2f2;
    --rule-grey:#cfcfcf;
    --text:#555555;
    --text-dark:#444444;
    --blue:#29a3e0;
    --blue-light:#5cc3f2;
    --white:#ffffff;
    --footer:#3d3d3d;
    --footer-deep:#2c2c2c;
    --box-dark:#333333;
  }
  *{box-sizing:border-box;margin:0;padding:0}
  html,body{width:1145px;height:1200px;overflow:hidden;background:var(--white)}
  body{font-family:"Open Sans",Arial,sans-serif;color:var(--text)}
  .page{position:relative;width:1050px;height:1100px;transform:scale(1.0905,1.0909);transform-origin:0 0}
  .abs{position:absolute;white-space:nowrap}
  a{color:inherit;text-decoration:none}

  .site-header{left:0;top:0;width:1050px;height:118px;background:linear-gradient(#2f2f2f,var(--header-mid))}
  .services-band{left:0;top:118px;width:1050px;height:319px;background:var(--panel-grey);border-bottom:3px solid var(--rule-grey)}

  .brand{left:34px;top:22px;font-size:40px;font-weight:600;color:var(--white);letter-spacing:-0.5px}
  .search{left:786px;top:32px;width:210px;height:28px;border-radius:14px;background:#1b1b1b;box-shadow:inset 0 1px 3px #000,0 1px 0 #666;font-size:11px;font-style:italic;color:#aaa;padding:7px 0 0 22px}
  .search-icon{left:972px;top:28px}

  .main-nav{left:36px;top:93px;width:710px;height:51px;background:linear-gradient(#fff,#eaeaea);border-radius:4px;box-shadow:0 2px 3px rgba(0,0,0,.25);display:flex;overflow:hidden}
  .main-nav a{display:flex;align-items:center;justify-content:center;font-size:13px;color:var(--text-dark);border-right:1px solid #dcdcdc}
  .main-nav a.active{background:linear-gradient(#5ccaf6,#1e9ee0);color:#111}

  .call{right:39px;top:89px;font-size:19px;color:var(--white);text-align:right}
  .call span{color:var(--blue-light)}
  .email{right:39px;top:122px;font-size:16px;color:var(--text);text-align:right}
  .email span{color:var(--blue)}

  .services-title{left:60px;top:174px;font-size:17px;color:var(--blue)}
  .services-list{left:66px;top:207px;list-style:none}
  .services-list li{height:27px;font-size:12px;color:var(--text);padding-left:17px;position:relative}
  .services-list li::before{content:"";position:absolute;left:0;top:5px;border-left:5px solid #777;border-top:4px solid transparent;border-bottom:4px solid transparent}

  .slider{left:396px;top:181px;width:604px;height:285px;background:var(--white);border:1px solid #ccc;box-shadow:0 10px 8px -6px rgba(0,0,0,.35)}
  .slide{position:absolute;left:6px;top:6px;width:591px;height:272px;background:radial-gradient(circle at 55% 30%,#ffffff,#e9e9ec 80%)}
  .values{position:absolute;left:68px;top:43px;list-style:none;font-family:"Arimo",Arial,sans-serif}
  .values li{height:46px;font-size:22px;color:var(--text-dark);display:flex;align-items:flex-start;gap:15px}
  .values li::before{content:"";width:17px;height:17px;margin-top:5px;border-radius:50%;background:#555}
  .slide-visual{position:absolute;left:238px;top:20px;width:353px;height:252px;background:linear-gradient(90deg,rgba(255,255,255,0),#d9d4cf 35%,#b07a4c 80%,#f3efea)}
  .slide-arrow{width:31px;height:31px;background:#fff;border:1px solid #ccc}

  .welcome-title{left:36px;top:483px;font-size:23px;color:var(--blue)}
  .welcome-copy{left:35px;top:520px;width:670px;font-size:12px;line-height:20px;color:var(--text);white-space:normal}
  .welcome-copy p{margin-bottom:8px}

  .newsletter{left:719px;top:496px;width:295px;height:164px;background:linear-gradient(#3d3d3d,#2d2d2d);border-radius:4px}
  .newsletter-icon{position:absolute;left:8px;top:6px;width:42px;height:38px;background:linear-gradient(#f4f4f4,#aab6c2);border-radius:3px;transform:rotate(-12deg)}
  .newsletter h3{position:absolute;left:59px;top:14px;font-size:17px;font-weight:400;color:var(--white)}
  .newsletter .field{position:absolute;left:21px;top:61px;width:257px;height:35px;background:#fff;border-radius:5px;font-size:11px;font-style:italic;color:#888;padding:11px 0 0 17px}
  .newsletter .submit{position:absolute;left:202px;top:113px;width:75px;height:29px;border-radius:4px;background:linear-gradient(#5ccaf6,#1e9ee0);color:#fff;font-size:14px;font-weight:700;text-align:center;line-height:29px}

  .divider{left:35px;top:689px;width:979px;border-top:2px dashed #b5b5b5}

  .section-icon{border-radius:3px}
  .news-icon{left:36px;top:709px;width:38px;height:33px;background:linear-gradient(#f0f0f0,#bdbdbd)}
  .gavel-icon{left:326px;top:712px;width:60px;height:32px;background:linear-gradient(90deg,#7a3d14,#b8733a)}
  .section-title{font-size:17px;color:var(--blue)}
  .news-title{left:89px;top:715px}
  .pubs-title{left:399px;top:715px}

  .news-list{left:36px;top:764px;list-style:none}
  .news-list li{height:71px;padding-left:14px;position:relative;font-size:11.5px;line-height:18px;color:var(--text)}
  .news-list li::before{content:"";position:absolute;left:0;top:4px;border-left:5px solid #555;border-top:4px solid transparent;border-bottom:4px solid transparent}
  .news-list strong{display:block;font-weight:400;color:var(--blue)}

  .pub-list{list-style:none;font-size:11.5px;color:var(--text-dark)}
  .pub-list li{height:28px}
  .pub-list a{border-bottom:1px solid #888;padding-bottom:1px}
  .pub-list a.current{color:var(--blue);border-color:var(--blue)}
  .pubs-a{left:322px;top:766px}
  .pubs-b{left:646px;top:766px}

  .site-footer{left:0;top:981px;width:1050px;height:119px;background:linear-gradient(#444,#333);border-top:1px solid #222}
  .footer-links{left:37px;top:1005px;height:23px;display:flex;align-items:center;font-size:10.5px;color:var(--white)}
  .social{display:flex;gap:11px;margin-left:10px}
  .social span{width:23px;height:23px;background:#4a7bb0;border:1px solid #6c8fb8}
  .copyright{left:37px;top:1045px;font-size:10.5px;color:var(--white)}

  .contact-box{left:668px;top:982px;width:346px;height:91px;background:var(--footer-deep);border-radius:0 0 5px 5px}
  .contact-box .label{position:absolute;left:16px;top:55px;font-size:11px;color:var(--white)}
  .contact-box .phone-icon{position:absolute;left:26px;top:18px}
  .address,.numbers{position:absolute;top:10px;font-size:10.5px;line-height:18px;color:#c9c9c9;white-space:nowrap}
  .address{left:90px}
  .numbers{left:205px}
</style>
</head>
<body>
<div class="page">
  <header class="site-header abs"></header>
  <div class="services-band abs"></div>

  <div class="brand abs">brinton law</div>
  <div class="search abs">Search</div>
  <svg class="search-icon abs" width="42" height="42" viewBox="0 0 42 42" aria-hidden="true">
    <line x1="24" y1="24" x2="38" y2="36" stroke="#333" stroke-width="5" stroke-linecap="round"/>
    <circle cx="17" cy="17" r="14" fill="#2f9ee6" stroke="#cfe9fb" stroke-width="2"/>
    <ellipse cx="13" cy="12" rx="6" ry="4" fill="#9fd6fb"/>
  </svg>

  <nav class="main-nav abs">
    <a class="active" href="#" style="width:108px">Home</a>
    <a href="#" style="width:105px">About Us</a>
    <a href="#" style="width:125px">Areas of Law</a>
    <a href="#" style="width:123px">Publications</a>
    <a href="#" style="width:111px">Our Prople</a>
    <a href="#" style="width:138px;border-right:0">Contact Us</a>
  </nav>

  <div class="call abs">Call Us : <span>(02) 9000 4821</span></div>
  <div class="email abs">E-mail : <span>info@brintonlaw.com.au</span></div>

  <h2 class="services-title abs" style="font-weight:400">Our Services</h2>
  <ul class="services-list abs">
    <li>Buying and selling businesses and companies</li>
    <li>Financing</li>
    <li>Leasing</li>
    <li>Property transactions</li>
    <li>Joint ventures</li>
    <li>Business restructuring</li>
    <li>Contract review and advice</li>
    <li>Employment Law Documentation, e.g. AWAs</li>
  </ul>

  <div class="slider abs">
    <div class="slide">
      <ul class="values">
        <li>Efficiency</li>
        <li>Fulfillment</li>
        <li>Integrity</li>
        <li>Teamwork</li>
      </ul>
      <div class="slide-visual" role="img" aria-label="Photo of a smiling lawyer in shirt and tie beside a wooden gavel"></div>
    </div>
  </div>
  <svg class="slide-arrow abs" style="left:382px;top:293px" viewBox="0 0 31 31" aria-hidden="true"><path d="M19 9 L11 15.5 L19 22Z" fill="#666"/></svg>
  <svg class="slide-arrow abs" style="left:984px;top:293px" viewBox="0 0 31 31" aria-hidden="true"><path d="M12 9 L20 15.5 L12 22Z" fill="#666"/></svg>

  <h1 class="welcome-title abs" style="font-weight:400">Welcome to our site</h1>
  <div class="welcome-copy abs">
    <p>Brinton Law is a dynamic commercial law firm in the CBD of Sydney providing services to corporate, small business and private clients.</p>
    <p>Brinton Law brings together over 30 years of experience in legal practice.</p>
    <p>The strong focus of the firm is on commercial law and estate planning.</p>
    <p>Brinton Law is committed to providing quality legal services in helping its clients achieve their objectives by providing a proactive understanding of its clients' businesses and creative legal solutions.</p>
  </div>

  <aside class="newsletter abs">
    <div class="newsletter-icon" role="img" aria-label="Envelope with letter illustration"></div>
    <h3>News Letter Signup</h3>
    <div class="field">Enter mail ID</div>
    <div class="submit">SUBMIT</div>
  </aside>

  <div class="divider abs"></div>

  <div class="section-icon news-icon abs" role="img" aria-label="Newspaper illustration"></div>
  <h2 class="section-title news-title abs" style="font-weight:400">Latest news</h2>
  <ul class="news-list abs">
    <li><strong>Undertakes laborious physical exercise</strong>Except to obtain some advantage from it<br>But who has any right to find.</li>
    <li><strong>Undertakes laborious physical exercise</strong>Except to obtain some advantage from it<br>But who has any right to find.</li>
    <li><strong>Undertakes laborious physical exercise</strong>Except to obtain some advantage from it<br>But who has any right to find.</li>
  </ul>

  <div class="section-icon gavel-icon abs" role="img" aria-label="Wooden gavel illustration"></div>
  <h2 class="section-title pubs-title abs" style="font-weight:400">Our Publications</h2>
  <ul class="pub-list pubs-a abs">
    <li><a href="#">Commencement of the Succession Act 2006 25.03.08</a></li>
    <li><a href="#">Is that will valid? 15.01.08</a></li>
    <li><a class="current" href="#">Labor's proposed changes to IR laws 14.12.07</a></li>
    <li><a href="#">Should you make your own will? 14.11.07</a></li>
    <li><a href="#">Illegal workers 14.08.07</a></li>
    <li><a href="#">Correct use of ACNs and ABNs 14.08.07</a></li>
    <li><a href="#">Power of Attorney Infosheet 10.08.07</a></li>
  </ul>
  <ul class="pub-list pubs-b abs">
    <li><a href="#">Intestate Estates Infosheet 08.08.07</a></li>
    <li><a href="#">Estate Planning Infosheet 07.06.07</a></li>
    <li><a href="#">Special Disability Trusts Infosheet 18.05.07</a></li>
    <li><a href="#">Testamentary Trusts Infosheet 17.05.07</a></li>
    <li><a href="#">Appointment of an Enduring Guardian Infosheet 15.05.07</a></li>
    <li><a href="#">Employees' liability for misleading or deceptive conduct 14.08.07</a></li>
  </ul>

  <footer class="site-footer abs"></footer>
  <div class="footer-links abs">
    <span>Home | About Us | Area of Law | Our People | Publication | Contact | Sitemap | Connect with us</span>
    <span class="social" aria-label="Social links"><span></span><span></span><span></span></span>
  </div>
  <div class="copyright abs">Copyright © 2012 www.brintonlaw.com.au &nbsp; All rights reserved</div>

  <div class="contact-box abs">
    <svg class="phone-icon" width="32" height="30" viewBox="0 0 32 30" aria-hidden="true">
      <path d="M2 9 Q16 0 30 9 L27 13 L22 11 L22 8 Q16 6 10 8 L10 11 L5 13Z" fill="#ddd"/>
      <path d="M8 14 L24 14 L29 28 L3 28Z" fill="#ddd"/>
      <circle cx="16" cy="21" r="3.5" fill="#2c2c2c"/>
    </svg>
    <div class="label">Contact us</div>
    <div class="address">Brinton Law Pty Ltd<br>Level 8<br>48 Clarence St<br>Sydney NSW 2000</div>
    <div class="numbers">Telephone: (02) 9000 4821<br>Facsimile: &nbsp;(02) 9000 4830<br>info@brintonlaw.com.au</div>
  </div>
</div>
</body>
</html>
```